Staff Newsletter Template Image

We are looking for two .jpg images that we can put into a Word document and use for our staff newsletter. We will then add content using text boxes.
Attached is the current template which works for the columns and size that we need but we just want a fresh new design.
The Word document shows how we use it.
The name will stay the same - Brightwave Post but can be a different look to the current one.

Target Market(s)

Sales team

Colors

Designer to choose colors to be used in the design.

Requirements
Must have
• Colours will be green, grey and white, possibly cream if needed. All from the guidelines.
• I have attached our brand guidelines which shows design elements and fonts for our brand. Also attached is brand guidelines for one of our product lines as we would like to use the same green.
• It needs to be nice to look at and motivational for our team

```html
<!DOCTYPE html>
<html lang="en">
<head>
<meta charset="utf-8">
<title>Brightwave Post – Staff Newsletter</title>
<link rel="stylesheet" href="https://fonts.googleapis.com/css2?family=Montserrat:wght@400&display=swap">
<style>
  :root {
    --leaf-green: #8cc63f;
    --charcoal: #3b3c3d;
    --slate: #565759;
    --paper: #ffffff;
    --mist-green: #f3f8ec;
  }
  html, body {
    margin: 0;
    padding: 0;
    overflow: hidden;
    background: var(--paper);
  }
  .newsletter-page {
    position: relative;
    width: 884px;
    height: 1200px;
    overflow: hidden;
    background: var(--paper);
  }
  .page-art {
    position: absolute;
    inset: 0;
    width: 884px;
    height: 1200px;
    display: block;
  }
  .masthead-wave-green { fill: var(--leaf-green); }
  .masthead-wave-dark { fill: var(--charcoal); }
  .footer-wave-slate { fill: var(--slate); }
  .footer-wave-dark { fill: var(--charcoal); }
  .footer-wave-green { fill: var(--leaf-green); }

  .background-name {
    position: absolute;
    left: 0;
    right: 0;
    top: 622px;
    margin: 0;
    text-align: center;
    font-family: "Montserrat", Arial, sans-serif;
    font-weight: 400;
    font-size: 54px;
    line-height: 1;
    color: var(--mist-green);
  }
  .footer-brand {
    position: absolute;
    right: 36px;
    top: 1118px;
    display: flex;
    align-items: center;
    gap: 8px;
  }
  .footer-brand-dot {
    width: 9px;
    height: 9px;
    border-radius: 50%;
    background: var(--paper);
  }
  .footer-brand-name {
    margin: 0;
    font-family: "Montserrat", Arial, sans-serif;
    font-weight: 400;
    font-size: 16px;
    line-height: 1;
    color: var(--paper);
  }
</style>
</head>
<body>
<main class="newsletter-page">
  <svg class="page-art" viewBox="0 0 884 1200" aria-hidden="true">
    <path class="masthead-wave-dark" d="M0,122 C120,160 260,180 400,150 C540,118 640,78 760,66 C640,90 500,155 360,195 C230,230 90,218 0,190 Z"/>
    <path class="masthead-wave-green" d="M0,0 H884 V26 C700,34 540,100 380,140 C250,168 110,152 0,115 Z"/>
    <path class="footer-wave-slate" d="M0,1058 C150,1082 300,1092 450,1072 C600,1048 700,1010 826,1012 C860,1013 884,1025 884,1040 V1200 H0 Z"/>
    <path class="footer-wave-dark" d="M0,1108 C200,1120 400,1088 550,1052 C680,1022 780,1008 884,1040 V1200 H0 Z"/>
    <path class="footer-wave-green" d="M0,1106 C160,1122 320,1148 540,1160 C360,1170 160,1178 0,1178 Z"/>
  </svg>

  <p class="background-name">Brightwave Post</p>

  <div class="footer-brand">
    <span class="footer-brand-dot"></span>
    <p class="footer-brand-name">Brightwave Post</p>
  </div>
</main>
</body>
</html>
```